Mobile Web App Design for Wellness Company

We already do have a website design developed at this address:
http://new.meadowbalancellc.com/

We need mobile web design. Not a mobile application design. We need design for what visitors would see when they visit http://new.meadowbalancellc.com/ on their mobile phones.

Mobile Web App design need to be similar to design of the actual website, please check from the address.

We need design for below pages:
- Home
- Biodynamic Craniosacral Therapy
- Biodynamic Lymphatic Drainage
- Chi Gong
- Contact Us
- About Us

We want easy access and obvious locations for navigate and call functionality.

We put together a design for mobile already but it's not good. Feel free to take the content from the website and/or mobile web app we designed to show your design with the actual content.

Design files must be high quality. We want designer to encorporate header images for the actual website we placed into mobile pages. For example, there's a header photo for each services, when visited in mobile, we'd like those images to show up too.

Most important part of this design will be easy of use and minimalist mobile focused design.

Good Luck!

Industry/Entity Type

Health And Wellness

Number of Pages Required

5+ page

Requirements
Must have
• Most important part of this design will be easy of use and minimalist mobile focused design.
Nice to have
• New up to date looking calming design
Should not have
• Dark background color

```html
<!DOCTYPE html>
<html lang="en">
<head>
<meta charset="utf-8">
<title>About Us – Meadow Balance Wellness</title>
<link href="https://fonts.googleapis.com/css2?family=Great+Vibes&family=Lora:wght@700&family=Open+Sans:wght@400;600&display=swap" rel="stylesheet">
<style>
  :root {
    --brand-blue: #1f5fa8;
    --brand-navy: #1d3f73;
    --text: #4a4a4a;
    --heading: #2b2b2b;
    --topbar: #f1f1f1;
    --icon: #8d8d8d;
    --teal-rule: #5fb3b6;
    --white: #ffffff;
  }
  * { box-sizing: border-box; margin: 0; padding: 0; }
  html, body { width: 1200px; height: 4648px; overflow: hidden; }
  body { background: var(--white); font-family: "Open Sans", Arial, sans-serif; color: var(--text); }

  .topbar { height: 120px; background: var(--topbar); display: flex; align-items: center; justify-content: space-between; padding: 0 48px; }
  .topbar__contacts { display: flex; gap: 44px; align-items: center; }
  .topbar__social { width: 44px; height: 44px; border-radius: 50%; background: var(--icon); }

  .site-header { height: 280px; display: flex; align-items: center; justify-content: space-between; padding: 0 48px; }
  .brand-name { font-family: "Open Sans", Arial, sans-serif; font-weight: 600; font-size: 68px; color: var(--brand-blue); line-height: 1; }
  .menu-toggle { width: 128px; height: 128px; border-radius: 50%; border: 5px solid #9aa7b5; display: flex; align-items: center; justify-content: center; }

  .page-hero { position: relative; height: 520px; background: linear-gradient(180deg, #5f8fc4 0%, #a9c6e3 38%, #7fa6cf 55%, #3a6ea8 70%, #7d7a73 86%, #4d4b47 100%); display: flex; align-items: center; justify-content: center; }
  .page-hero__title { font-family: "Great Vibes", cursive; font-size: 150px; color: var(--white); font-weight: 400; text-shadow: 0 4px 10px rgba(0,0,0,0.25); }

  .about { padding: 128px 48px 0; }
  .about__heading { font-family: "Lora", Georgia, serif; font-weight: 700; font-size: 64px; color: var(--heading); margin-bottom: 64px; }
  .about__text { font-size: 43px; line-height: 84px; margin-bottom: 84px; }
  .about__text:last-of-type { margin-bottom: 104px; }

  .studio-photo { height: 1332px; background: linear-gradient(160deg, #e8dc95 0%, #d8c571 35%, #b79f4c 60%, #6b6a5e 82%, #3c4a5a 100%); }

  .rule { height: 5px; background: var(--teal-rule); margin: 132px 48px 0; }

  .site-footer { text-align: center; padding-top: 108px; }
  .site-footer .brand-name { font-size: 62px; color: var(--brand-navy); }
  .site-footer__copy { font-size: 42px; line-height: 84px; margin-top: 44px; }
</style>
</head>
<body>
  <div class="topbar">
    <div class="topbar__contacts">
      <svg width="44" height="44" viewBox="0 0 24 24" aria-label="Call"><path fill="#8d8d8d" d="M6.6 10.8a15 15 0 0 0 6.6 6.6l2.2-2.2c.3-.3.7-.4 1-.2 1.1.4 2.3.6 3.6.6.6 0 1 .4 1 1V20c0 .6-.4 1-1 1A17 17 0 0 1 3 4c0-.6.4-1 1-1h3.5c.6 0 1 .4 1 1 0 1.3.2 2.5.6 3.6.1.3 0 .7-.2 1z"/></svg>
      <svg width="48" height="40" viewBox="0 0 24 20" aria-label="Email"><rect x="1" y="2" width="22" height="16" rx="1.5" fill="#8d8d8d"/><path d="M2 3l10 8 10-8" fill="none" stroke="#f1f1f1" stroke-width="1.8"/></svg>
    </div>
    <span class="topbar__social" aria-label="Social page"></span>
  </div>

  <header class="site-header">
    <div class="brand-name">Meadow Balance</div>
    <div class="menu-toggle" aria-label="Menu">
      <svg width="56" height="48" viewBox="0 0 28 24"><rect y="2" width="28" height="4" rx="2" fill="#1d3f73"/><rect y="10" width="28" height="4" rx="2" fill="#1d3f73"/><rect y="18" width="28" height="4" rx="2" fill="#1d3f73"/></svg>
    </div>
  </header>

  <section class="page-hero" role="img" aria-label="Balanced stones over a calm sea under a blue sky">
    <h1 class="page-hero__title">About Us</h1>
  </section>

  <main class="about">
    <h2 class="about__heading">A few word about us</h2>
    <p class="about__text">At Meadow Balance Wellness, my mission is to create a space where my clients can feel a sense of safety, peace, comfort, and support; tap into the resources for healing that all of us are given when we come into the world; and achieve deep rest that, for many, leads to profound change.</p>
    <p class="about__text">My primary tools for working with clients are Biodynamic Craniosacral Therapy, Biodynamic Lymphatic Drainage, and Chi Gong; when appropriate, I also incorporate essential oils in my work.</p>
    <p class="about__text">For information on my services, please visit our Services page. Additional information about costs can be found on the Pricing page.</p>
    <div class="studio-photo" role="img" aria-label="Warm treatment room with a blue sofa, coffee table, bookshelf and lamps"></div>
  </main>

  <div class="rule"></div>

  <footer class="site-footer">
    <div class="brand-name">Meadow Balance</div>
    <p class="site-footer__copy">2017, Meadow Balance Wellness LLC. All Rights Reserved.<br>Helping you rediscover your inner resources for wellness</p>
  </footer>
</body>
</html>
```